Velk Partners Building Business Cards

We need a business card that reflects our business as "Solar Experts" in San Diego. Browse our website www.velkpartners.example our License needs to be displayed as "CSLB# 3867140" our phone number is (619) 555-0187

Save thousands on your electric bills and increase the value of your home while helping to protect the environment. Our solar installation experts will help you design the system that's right for you, using only the highest quality equipment that will look great and give you ideal performance. Our goal is to make you energy independent, and get your electric bill to 0.

Paul Osterby
(619) 555-0187
paul@velkpartners.example

Target Market(s)

Home owners in san diego looking for solar

Industry/Entity Type

Solar Energy

Contact Information for Business Card

Paul Osterby
(619) 555-0187
paul@velkpartners.example

Font styles to use
Other font styles liked:
• Use our logo font

Requirements
Must have
• License needs to be displayed as "CSLB# 3867140" our phone number is (619) 555-0187
Nice to have
• Real images of rooftop home solar in san diego
Should not have
• our business address

```html
<!DOCTYPE html>
<html lang="en">
<head>
<meta charset="utf-8">
<title>Velk Partners Building – Business Card</title>
<link rel="stylesheet" href="https://fonts.googleapis.com/css2?family=Roboto:wght@400;500;700&display=swap">
<style>
  :root {
    --page: #e8e3dc;
    --card-face: #eef0f1;
    --card-edge: #d9dcde;
    --navy: #2c4a7e;
    --gold: #eba81c;
    --ink: #1f3152;
    --ink-soft: #36404c;
    --white: #ffffff;
  }
  * { margin: 0; padding: 0; box-sizing: border-box; }
  html, body {
    width: 1200px;
    height: 1200px;
    overflow: hidden;
    background: var(--page);
    font-family: "Roboto", Arial, sans-serif;
  }
  .card {
    position: absolute;
    left: 100px;
    top: 304px;
    width: 1000px;
    height: 592px;
    background: var(--card-face);
    border: 1px solid var(--card-edge);
    box-shadow: 0 18px 40px rgba(60, 50, 40, 0.18);
    overflow: hidden;
  }
  .card-art {
    position: absolute;
    inset: 0;
    width: 1000px;
    height: 592px;
  }
  .brand {
    position: absolute;
    left: 0;
    top: 270px;
    width: 460px;
    text-align: center;
    color: var(--white);
    font-weight: 500;
    font-size: 31px;
    letter-spacing: 0.3px;
  }
  .brand-dot {
    position: absolute;
    left: 200px;
    top: 180px;
    width: 64px;
    height: 64px;
    border-radius: 50%;
    background: var(--gold);
  }
  .contact {
    position: absolute;
    left: 557px;
    top: 164px;
    color: var(--ink-soft);
  }
  .contact-name {
    font-size: 35px;
    font-weight: 700;
    color: var(--ink);
    line-height: 1.1;
  }
  .contact-title {
    font-size: 22px;
    margin-top: 6px;
  }
  .contact-list {
    list-style: none;
    margin-top: 38px;
  }
  .contact-list li {
    display: flex;
    align-items: center;
    font-size: 24px;
    line-height: 35px;
  }
  .contact-list svg {
    width: 24px;
    height: 24px;
    margin-right: 26px;
    fill: var(--gold);
    flex: none;
  }
  .accent { color: var(--gold); }
  .license {
    font-size: 24px;
    margin-top: 8px;
  }
</style>
</head>
<body>
  <div class="card">
    <svg class="card-art" viewBox="0 0 1000 592" aria-hidden="true">
      <path fill="var(--gold)" d="M447 0 C470 80 500 200 490 330 C482 430 440 520 412 592 H432 C462 520 506 430 512 330 C520 200 488 80 461 0 Z"/>
      <path fill="var(--navy)" d="M0 0 H447 C470 80 500 200 490 330 C482 430 440 520 412 592 H0 Z"/>
    </svg>

    <div class="brand-dot"></div>
    <div class="brand">Velk Partners Building</div>

    <div class="contact">
      <div class="contact-name">Paul Osterby</div>
      <div class="contact-title">Managing Director</div>
      <ul class="contact-list">
        <li>
          <svg viewBox="0 0 24 24"><path d="M3 8c0-2 2-3 9-3s9 1 9 3v2h-5V8H8v2H3z M6 12h12l2 7H4z M12 13.5a2.5 2.5 0 1 0 0 5a2.5 2.5 0 0 0 0-5z"/></svg>
          (619) 555-0187
        </li>
        <li>
          <svg viewBox="0 0 24 24"><path d="M12 2a10 10 0 1 0 0 20a10 10 0 0 0 0-20zm0 2c.9 0 2.3 2 2.8 5H9.2C9.7 6 11.1 4 12 4zM4.3 9h2.9a18 18 0 0 0 0 6H4.3a8 8 0 0 1 0-6zm4.9 0h5.6a16 16 0 0 1 0 6H9.2a16 16 0 0 1 0-6zm7.6 0h2.9a8 8 0 0 1 0 6h-2.9a18 18 0 0 0 0-6zM9.2 17h5.6c-.5 3-1.9 5-2.8 5s-2.3-2-2.8-5z"/></svg>
          paul@velkpartners.example
        </li>
        <li>
          <svg viewBox="0 0 24 24"><path d="M2 5h20v14H2z" opacity="0.9"/><path d="M2 5l10 8l10-8" fill="none" stroke="var(--card-face)" stroke-width="1.6"/></svg>
          <span>www.<span class="accent">velkpartners</span>.example</span>
        </li>
      </ul>
      <div class="license">License: CSLB# 3867140</div>
    </div>
  </div>
</body>
</html>
```